RWT Fittings Ltd Business Cards

We need a business card with our business logo. We provide window and door installations on high-rises in west coast British Colombia, Canada.

I would like my business information and details on one side of the card, and the other side the company name with logo

Target Market(s)

General Contractors

Industry/Entity Type

Construction

Contact Information for Business Card

one side i want my company name and logo in the dark theme logo that i provided

Requirements
Must have
• Marco Peltieri, 16045518293, RWTFittings@mailbox-demo.com, 1407-5194 Linden Row Burnaby BC, V5H 2K9, Owner & Manager

```html
<!DOCTYPE html>
<html lang="en">
<head>
<meta charset="utf-8">
<title>RWT Fittings Ltd — Business Cards</title>
<link rel="stylesheet" href="https://fonts.googleapis.com/css2?family=Montserrat:wght@400;500;600&display=swap">
<style>
  :root {
    --stage-top: #8a8a8a;
    --stage-bottom: #5a5a5a;
    --card-white: #ffffff;
    --card-dark-top: #2a2826;
    --card-dark-bottom: #141312;
    --brand-blue: #29a3e0;
    --brand-blue-light: #4cc0f0;
    --text-grey: #6f6f6f;
    --rule-grey: #c4c4c4;
  }
  * { box-sizing: border-box; margin: 0; padding: 0; }
  html, body { width: 1200px; height: 876px; overflow: hidden; }
  body {
    background: radial-gradient(ellipse at 50% 40%, var(--stage-top), var(--stage-bottom));
    font-family: "Montserrat", sans-serif;
    display: flex;
    align-items: center;
    justify-content: center;
    gap: 44px;
  }
  .card {
    width: 530px;
    height: 303px;
    border-radius: 4px;
    position: relative;
    overflow: hidden;
    box-shadow: 0 14px 30px rgba(0,0,0,0.35);
  }

  /* Front: contact side */
  .card--front { background: var(--card-white); display: flex; align-items: center; }
  .card--front .brand {
    width: 46%;
    display: flex;
    align-items: center;
    justify-content: center;
    gap: 10px;
  }
  .brand__mark { width: 16px; height: 16px; background: var(--brand-blue); flex: none; }
  .brand__name {
    color: var(--brand-blue);
    font-weight: 600;
    font-size: 21px;
    letter-spacing: 0.5px;
    white-space: nowrap;
  }
  .divider { width: 1px; height: 150px; background: var(--rule-grey); flex: none; }
  .details { padding-left: 26px; color: var(--text-grey); font-size: 12.5px; line-height: 1.55; }
  .details__name {
    color: var(--brand-blue);
    font-weight: 500;
    font-size: 24px;
    letter-spacing: 2px;
    text-transform: uppercase;
    line-height: 1.1;
    white-space: nowrap;
  }
  .details__title { margin-bottom: 2px; }
  .details__contacts { list-style: none; margin-top: 8px; }
  .details__contacts li { display: flex; align-items: center; gap: 7px; white-space: nowrap; }
  .details__contacts svg { width: 11px; height: 11px; fill: var(--brand-blue); flex: none; }
  .band {
    position: absolute;
    left: 46%;
    right: 0;
    bottom: 0;
    height: 9px;
    background: var(--brand-blue);
  }

  /* Back: brand side */
  .card--back {
    background: linear-gradient(160deg, var(--card-dark-top), var(--card-dark-bottom));
    display: flex;
    align-items: center;
    justify-content: center;
  }
  .card--back .brand { display: flex; align-items: center; gap: 12px; }
  .card--back .brand__mark { width: 20px; height: 20px; background: var(--brand-blue-light); }
  .card--back .brand__name { color: var(--brand-blue-light); font-size: 28px; }
</style>
</head>
<body>
  <section class="card card--front" aria-label="Business card, contact side">
    <div class="brand">
      <span class="brand__mark"></span>
      <span class="brand__name">RWT Fittings Ltd</span>
    </div>
    <div class="divider"></div>
    <div class="details">
      <h1 class="details__name">Marco Peltieri</h1>
      <p class="details__title">Owner &amp; Manager</p>
      <p class="details__address">1407-5194 Linden Row, Burnaby<br>BC, V5H 2K9</p>
      <ul class="details__contacts">
        <li>
          <svg viewBox="0 0 24 24" aria-hidden="true"><path d="M6.6 10.8a15.1 15.1 0 0 0 6.6 6.6l2.2-2.2c.3-.3.7-.4 1-.2 1.1.4 2.3.6 3.6.6.6 0 1 .4 1 1V20c0 .6-.4 1-1 1A17 17 0 0 1 3 4c0-.6.4-1 1-1h3.5c.6 0 1 .4 1 1 0 1.3.2 2.5.6 3.6.1.3 0 .7-.2 1z"/></svg>
          (604) 551-8293
        </li>
        <li>
          <svg viewBox="0 0 24 24" aria-hidden="true"><path d="M2 5h20v14H2zm2 2v.5l8 5 8-5V7zm0 2.8V17h16V9.8l-8 5z"/></svg>
          RWTFittings@mailbox-demo.com
        </li>
        <li>
          <svg viewBox="0 0 24 24" aria-hidden="true"><path d="M12 2a10 10 0 1 0 0 20 10 10 0 0 0 0-20zm6.9 9h-3a15 15 0 0 0-1.3-5.6A8 8 0 0 1 18.9 11zM12 4c.9 1.2 1.8 3.6 1.9 7h-3.8c.1-3.4 1-5.8 1.9-7zM9.4 5.4A15 15 0 0 0 8.1 11h-3a8 8 0 0 1 4.3-5.6zM5.1 13h3a15 15 0 0 0 1.3 5.6A8 8 0 0 1 5.1 13zm6.9 7c-.9-1.2-1.8-3.6-1.900-7h3.8c-.1 3.4-1 5.8-1.9 7zm2.6-1.4a15 15 0 0 0 1.3-5.6h3a8 8 0 0 1-4.3 5.6z"/></svg>
          rwtfittings-demo.com
        </li>
      </ul>
    </div>
    <div class="band"></div>
  </section>

  <section class="card card--back" aria-label="Business card, brand side">
    <div class="brand">
      <span class="brand__mark"></span>
      <span class="brand__name">RWT Fittings Ltd</span>
    </div>
  </section>
</body>
</html>
```